Advanced Therapeutic Massage Therapist

I need a business card advertising my massage services as an advanced therapeutic massage therapist. I offer advanced therapeutic massage, swedish and deep tissue. I want to create a simple, professional and feminine card. I like bright colours and creativity.

I prefer a bold and experimental approach rather than something status-quo. A card to suggest therapeutic healing through dynamic massage. Motifs, shapes or layout which suggest movement and flow.
Updates

Target Market(s)

Everybody!

Industry/Entity Type

Health And Wellness

Contact Information for Business Card

The card should include:
My name, logo, services offered and my contact details.

Sláine Dunleavy
Massage Therapist

- Swedish - Deep Tissue - Advanced Therapeutic

Phone: (+353) 87 216 4093
Email: regenerate@slainedunleavy-example.com
Website: www.slainedunlevy-example.com

Font styles to use
Serif
Sans Serif
Decorative
Script

Colors

Designer to choose colors to be used in the design.

Requirements
Must have
• An example may contain something like this, yet concise:
• "Sláine Dunleavy
• Massage Therapist
• - Swedish - Deep Tissue - Advanced Therapeutic"
Nice to have
• This sentence is optional:
• Imagery such as a logo or symbol. I have attached a file containing a logo I had produced however the name is incorrect now as it is "Sláine" not "Nelly". It could be edited to change it to Sláine.
• I have sent the file as .psd .jpg. .pdf and .png
• I like when the card conveys energy, movement, pressure points, flow etc.
• I just like the designer to follow their own style and ideas. I like bright colours but must have a lot of a base colour to offset it. I really prefer them to follow their own inspiration. That is my preference.
Should not have
• Pine trees, non-native trees to Britain and Ireland, exotic flowers or animals that are not native to Britain and Ireland.
• I don't like brown as the background colour of the card.
• The cars shouldn't look like a wedding invitation i.e too many floral type designs.

```html
<!DOCTYPE html>
<html lang="en">
<head>
<meta charset="utf-8">
<title>Sláine Dunleavy – Massage Therapist Business Card</title>
<link rel="stylesheet" href="https://fonts.googleapis.com/css2?family=Kaushan+Script&family=Source+Sans+3:wght@400&display=swap">
<style>
  :root {
    --backdrop: #3d3d3d;
    --card-front: #080808;
    --card-back: #1c5a5f;
    --ink-light: #ffffff;
    --rule-accent: #a9d8c9;
    --mark-mint: #a9d8c9;
    --mark-mint-deep: #8cc2b3;
    --mark-ink: #5a3410;
  }
  html, body {
    margin: 0;
    padding: 0;
    width: 1200px;
    height: 900px;
    overflow: hidden;
    background: var(--backdrop);
  }
  .canvas {
    position: relative;
    width: 1200px;
    height: 900px;
  }
  .card {
    position: absolute;
    top: 215px;
    width: 414px;
    height: 414px;
    border-radius: 50%;
    box-shadow: 0 2px 6px rgba(0, 0, 0, 0.35);
  }
  .card--front {
    left: 164px;
    background: var(--card-front);
  }
  .card--back {
    left: 623px;
    background: var(--card-back);
    color: var(--ink-light);
    font-family: "Source Sans 3", "Myriad Pro", Arial, sans-serif;
    text-align: center;
  }
  .brand-mark {
    position: absolute;
    left: 207px;
    top: 207px;
    transform: translate(-50%, -50%);
    width: 236px;
    height: 236px;
  }
  .brand-mark__name {
    font-family: "Source Sans 3", "Myriad Pro", Arial, sans-serif;
    font-size: 21px;
    fill: var(--mark-ink);
  }
  .back-content {
    position: absolute;
    left: 0;
    right: 0;
    top: 52px;
  }
  .therapist-name {
    margin: 0;
    font-family: "Kaushan Script", cursive;
    font-weight: 400;
    font-size: 31px;
    line-height: 38px;
    letter-spacing: 0.5px;
  }
  .therapist-role,
  .contact-line,
  .service-line,
  .about-line {
    margin: 0;
    font-size: 19px;
    line-height: 24.5px;
  }
  .therapist-role { margin-top: 2px; }
  .contact { margin-top: 13px; }
  .divider {
    width: 204px;
    height: 0;
    border: 0;
    border-top: 1px solid var(--rule-accent);
    margin: 12px auto 12px;
  }
</style>
</head>
<body>
<main class="canvas">
  <section class="card card--front" aria-label="Card front">
    <svg class="brand-mark" viewBox="0 0 236 236" role="img" aria-label="Sláine Dunleavy brand mark area">
      <defs>
        <radialGradient id="markFill" cx="50%" cy="45%" r="55%">
          <stop offset="0%" stop-color="var(--mark-mint)"/>
          <stop offset="100%" stop-color="var(--mark-mint-deep)"/>
        </radialGradient>
      </defs>
      <circle cx="118" cy="118" r="108" fill="url(#markFill)"/>
      <text class="brand-mark__name" x="118" y="125" text-anchor="middle">Sláine Dunleavy</text>
    </svg>
  </section>

  <section class="card card--back" aria-label="Card back">
    <div class="back-content">
      <h1 class="therapist-name">Sláine Dunleavy</h1>
      <p class="therapist-role">Massage Therapist</p>
      <div class="contact">
        <p class="contact-line">(+353) 87 216 4093</p>
        <p class="contact-line">regenerate@slainedunleavy-example.com</p>
        <p class="contact-line">www.slainedunlevy-example.com</p>
      </div>
      <hr class="divider">
      <div class="services">
        <p class="service-line">Swedish | Deep Tissue</p>
        <p class="service-line">Advanced Therapeutic</p>
      </div>
      <hr class="divider">
      <div class="about">
        <p class="about-line">NTQA qualified specialising in</p>
        <p class="about-line">advanced therapeutic and</p>
        <p class="about-line">deep tissue massage</p>
      </div>
    </div>
  </section>
</main>
</body>
</html>
```